Harborline Auto LLC

Car Dealer Customer Service
Address: 2874 Cresthaven Road, Shelbyville, TN 37162
web: www.harborlineautoxq.net
email: harborlineautoxq@mailnest.example
Phone: (931) 555-0148
Phone: (629) 555-0173

```html
<!DOCTYPE html>
<html lang="en">
<head>
<meta charset="utf-8">
<title>Harborline Auto – Business Card</title>
<link rel="stylesheet" href="https://fonts.googleapis.com/css2?family=Bebas+Neue&family=Montserrat:wght@700;800&family=Roboto:wght@400&display=swap">
<style>
  :root {
    --amber: #ecb446;
    --ocean: #1a7aae;
    --ocean-deep: #1d6f9f;
    --frost: #f5f3f3;
    --frost-shade: #e6e2e2;
    --ink-light: #ffffff;
    --stage: #d9d6d6;
    --car-light: #f6ece9;
    --car-shade: #efd9d6;
  }
  * { box-sizing: border-box; margin: 0; padding: 0; }
  html, body {
    width: 1200px; height: 900px; overflow: hidden;
    background: var(--stage);
  }
  .canvas {
    width: 1200px; height: 900px;
    display: flex; align-items: center; justify-content: center;
  }
  .business-card {
    width: 1000px; height: 618px;
    display: flex;
    box-shadow: 0 14px 40px rgba(0,0,0,0.18);
  }
  .contact-side {
    position: relative;
    width: 472px; height: 100%;
    background: linear-gradient(to bottom, var(--amber) 0 390px, var(--ocean) 390px 100%);
    color: var(--ink-light);
    font-family: "Roboto", Arial, sans-serif;
  }
  .person-name {
    position: absolute; left: 44px; top: 70px;
    font-family: "Montserrat", Arial, sans-serif;
    font-weight: 800; font-size: 35px; letter-spacing: 0.2px;
  }
  .person-title {
    position: absolute; left: 44px; top: 108px;
    font-size: 28px;
  }
  .address {
    position: absolute; left: 44px; top: 166px;
    font-size: 27px; line-height: 37px; font-style: normal;
  }
  .car-illustration {
    position: absolute; left: 10px; top: 248px;
    width: 458px; height: 170px;
    border-radius: 90px 110px 40px 40px;
    background: radial-gradient(ellipse at 45% 45%, var(--car-light), var(--car-shade));
  }
  .contact-list {
    position: absolute; left: 44px; top: 428px;
    list-style: none;
  }
  .contact-list li {
    display: flex; align-items: center; gap: 10px;
    font-size: 27px; height: 36.5px;
  }
  .contact-list li.email { font-size: 21.5px; }
  .contact-list svg { width: 26px; height: 26px; flex: none; }
  .brand-side {
    flex: 1; position: relative;
    background: linear-gradient(160deg, var(--frost), var(--frost-shade));
    text-align: center;
  }
  .brand-dot {
    position: absolute; left: 50%; top: 148px;
    width: 190px; height: 190px; margin-left: -95px;
    border-radius: 50%;
    background: var(--ocean);
    opacity: 0.9;
  }
  .brand-name {
    position: absolute; left: 0; right: 0; top: 357px;
    font-family: "Montserrat", Arial, sans-serif;
    font-weight: 800; font-size: 44px;
    color: var(--ocean-deep);
  }
  .tagline {
    position: absolute; left: 0; right: 0; top: 430px;
    font-family: "Bebas Neue", Impact, sans-serif;
    font-size: 40px; color: var(--amber);
  }
</style>
</head>
<body>
<main class="canvas">
  <article class="business-card">
    <section class="contact-side">
      <h1 class="person-name">MARCUS DELANEY</h1>
      <p class="person-title">Managing Director</p>
      <address class="address">2874 Cresthaven Road<br>Shelbyville, TN 37162</address>
      <div class="car-illustration" role="img" aria-label="Illustration of a vintage car in light tones"></div>
      <ul class="contact-list">
        <li>
          <svg viewBox="0 0 24 24" fill="none" stroke="currentColor" stroke-width="2"><path d="M5 3h4l2 5-2.5 1.5a11 11 0 0 0 6 6L16 13l5 2v4a2 2 0 0 1-2 2A17 17 0 0 1 3 5a2 2 0 0 1 2-2z"/></svg>
          (931) 555-0148
        </li>
        <li>
          <svg viewBox="0 0 24 24" fill="none" stroke="currentColor" stroke-width="2"><path d="M5 3h4l2 5-2.5 1.5a11 11 0 0 0 6 6L16 13l5 2v4a2 2 0 0 1-2 2A17 17 0 0 1 3 5a2 2 0 0 1 2-2z"/></svg>
          (629) 555-0173
        </li>
        <li>
          <svg viewBox="0 0 24 24" fill="none" stroke="currentColor" stroke-width="1.8"><circle cx="12" cy="12" r="9.5"/><ellipse cx="12" cy="12" rx="4" ry="9.5"/><path d="M2.5 12h19M4 7h16M4 17h16"/></svg>
          www.harborlineautoxq.net
        </li>
        <li class="email">
          <svg viewBox="0 0 24 24" fill="currentColor"><path d="M2 5h20v14H2z" opacity="0"/><path d="M2 6h20v13H2zM3.5 7.5l8.5 6.5 8.5-6.5" fill="none" stroke="currentColor" stroke-width="1.8"/></svg>
          harborlineautoxq@mailnest.example
        </li>
      </ul>
    </section>
    <section class="brand-side">
      <div class="brand-dot"></div>
      <h2 class="brand-name">HARBORLINE AUTO</h2>
      <p class="tagline">Car Dealer Customer Service</p>
    </section>
  </article>
</main>
</body>
</html>
```